Im want a website LIKE VRX's and FleetHollow.com's with product payment options like Trenzo's

I need a website LIKE VRX with a header made EXACTLY LIKE THAT OF FLEETHOLLOWS .

The front page photo should be like that of FLEETHOLLOW's webpage as well.

The name of the website will be called "M.K. (Caldera Key)".

We will be targeting ALL MARKETS in a small town in central Panama and charging businesses "listing fees" like a phone book does but also providing informational blogs, news, and other interesting activities.

THIS IS A MULTI PAGE WEBSITE

THIS IS WHERE VRX's website meets Brivelle/FleetHollow.

Once the layout is built I will tweak and modify, add information, and upload items for sale.

Here is a list of specific categories that should be listed out above the front page header image/search bar

-- Home -- News -- Travel -- Activities -- Shop & Dine -- Store -- More... --

These categories should be spread across the bottom of the page in three sections:

WHATS SO GREAT ABOUT (Caldera Key),
HAND PICKED TOURS
ACTIVITIES etc.

Also lets use www.Trenzo.example 's
"HOT DESTINATIONS"
"BEAT THE BEST PRICES IN BOQUETE"
"OCTOBERS INSIDER PICKS"
"TOP DESTINATIONS"
and spread them in four sections side-by-side near the bottom of the page.

Overall I would like to see the finished product to be something LIKE VRX's and FleetHollows.

WE NEED ONLINE PAYMENT OPTIONS LIKE BRIVELLE'S WEBSITE HAS

This will be a desktop website but should be very mobile friendly as well.

-rodmund

P.S. Good luck!

If it isn't already too late to change the website name, the name of the website should be "Caldera Key". Added Friday, October 9, 2015

What do you guys think the budget should be to win this? Added Saturday, October 10, 2015

www.palmorra.example is the most amazing simple site. Whoever can make me a replica with my specifications will win immediately!!!! Added Sunday, October 18, 2015

OMG www.palmorra.example is the bomb!So simple and elegant. Whoever can make me an EXACT REPLICA OF WWW.PALMORRA.EXAMPLE as my site with the specifications mentioned in my brief will take home the $825.00 immediately! Good luck amigos! Added Sunday, October 18, 2015

Does anybody know how to add recurring monthly billing options on this website? Added Sunday, October 18, 2015

ALL MARKETS

Product

Coded - Design and coding required

5+ page

• Coinvey payment options.
• I must be able to add and remove photos/text and video from the HTML files in the page.
• Be creative my friends, and may the odds be forever in your favor!
• I added some photos of a good layout for our page below.

```html
<!DOCTYPE html>
<html lang="en">
<head>
<meta charset="utf-8">
<title>Caldera Key – Tours, Hotels & Vehicles</title>
<link href="https://fonts.googleapis.com/css2?family=Montserrat:wght@400;600;700&family=Open+Sans:wght@400;600;700&display=swap" rel="stylesheet">
<style>
  :root{
    --blue:#1f3d8f;
    --blue-dark:#172f73;
    --blue-deep:#132865;
    --orange:#f26522;
    --text:#4a4a4a;
    --muted:#8a8a8a;
    --line:#e3e3e3;
    --white:#ffffff;
    --page:#f4f4f4;
  }
  *{box-sizing:border-box;margin:0;padding:0}
  html,body{width:694px;height:1200px;overflow:hidden}
  body{position:relative;background:var(--page);font-family:"Open Sans",Arial,sans-serif;color:var(--text);font-size:7px}
  .abs{position:absolute}

  .backdrop{left:0;top:0;width:694px;height:640px;background:linear-gradient(180deg,#7fc4e8 0%,#bfe6f5 35%,#3fb3c9 55%,#e9dcc0 80%,#f4f4f4 100%)}
  .page{left:46px;top:0;width:604px;height:944px;background:var(--white)}

  .topbar{left:140px;top:0;width:510px;height:58px;background:var(--blue)}
  .logo{left:46px;top:0;width:94px;height:58px;background:linear-gradient(160deg,#2a8fc0,#1a5f8a);display:flex;align-items:center;justify-content:center}
  .logo span{font-family:"Montserrat",sans-serif;font-weight:700;font-size:12px;color:var(--white);text-transform:uppercase;text-align:center;line-height:1.1}
  .helpline{left:345px;top:14px;color:var(--white)}
  .helpline small{display:block;font-size:6px;letter-spacing:.5px;opacity:.85}
  .helpline strong{font-family:"Montserrat",sans-serif;font-size:10px}
  .helpline svg{position:absolute;left:-16px;top:6px}
  .select{top:20px;height:14px;border:1px solid rgba(255,255,255,.5);color:var(--white);font-size:6px;padding:2px 4px;display:flex;justify-content:space-between;align-items:center}

  .nav{left:46px;top:58px;width:604px;height:19px;background:var(--blue-dark);display:flex}
  .nav a{color:var(--white);text-decoration:none;font-size:6.5px;font-weight:600;padding:0 11px;line-height:19px}
  .nav a.active{background:var(--orange)}

  .hero{left:46px;top:77px;width:604px;height:280px;background:
    linear-gradient(180deg,rgba(14,27,61,0) 55%,rgba(14,27,61,.2) 100%),
    linear-gradient(100deg,#0e1b3d 0%,#1c2f63 40%,#2c3f75 62%,#1a2548 100%)}
  .hero-road{left:46px;top:250px;width:604px;height:60px;background:linear-gradient(180deg,rgba(242,140,60,0) 0%,rgba(242,140,60,.55) 50%,rgba(26,37,72,0) 100%)}
  .hero-copy{left:460px;top:178px;width:180px;color:var(--white)}
  .hero-copy h2{font-family:"Montserrat",sans-serif;font-weight:700;font-size:16px;letter-spacing:.5px}
  .hero-copy p{font-size:6px;line-height:1.5;margin:4px 0 8px}
  .btn{display:inline-block;background:var(--orange);color:var(--white);font-family:"Montserrat",sans-serif;font-weight:700;font-size:6.5px;padding:5px 12px;letter-spacing:.5px}
  .dots{left:314px;top:323px;display:flex;gap:6px}
  .dots i{width:5px;height:5px;border-radius:50%;background:rgba(255,255,255,.5)}
  .dots i.on{background:var(--white)}

  .section-title{font-family:"Montserrat",sans-serif;font-weight:700;font-size:10px;color:#333}
  .arrows{display:flex;gap:4px}
  .arrows span{width:13px;height:13px;border:1px solid var(--line);border-radius:50%;display:flex;align-items:center;justify-content:center}

  .tour{top:395px;width:193px;height:172px;border:1px solid var(--line);background:var(--white);overflow:hidden}
  .tour .photo{height:92px}
  .ribbon{left:-1px;top:-1px;width:40px;height:40px;overflow:hidden}
  .ribbon b{position:absolute;left:-14px;top:9px;width:60px;transform:rotate(-45deg);background:var(--orange);color:var(--white);font-size:5px;text-align:center;padding:2px 0}
  .tour h3{font-size:6.5px;font-weight:700;color:var(--orange);text-transform:uppercase;line-height:1.35;padding:7px 8px 3px}
  .stars{color:var(--orange);font-size:7px;letter-spacing:1px}
  .stars em{color:var(--muted);font-style:normal;font-size:5.5px;letter-spacing:0;margin-left:3px}
  .tour .rating{padding:0 8px}
  .tour .meta{display:flex;justify-content:space-between;align-items:flex-end;padding:6px 8px 0;border-top:1px solid var(--line);margin:8px 0 0}
  .tour .meta small{font-size:5.5px;color:var(--muted)}
  .price{text-align:right}
  .price small{display:block}
  .price strong{font-family:"Montserrat",sans-serif;font-size:13px;color:#333;font-weight:600}

  .rental{left:46px;top:585px;width:604px;height:168px;background:linear-gradient(90deg,#3d4046 0%,#8a8e95 35%,#5c6068 60%,#2f3237 100%)}
  .rental-copy{left:398px;top:618px;width:200px;color:var(--white)}
  .rental-copy h2{font-family:"Montserrat",sans-serif;font-weight:700;font-size:16px}
  .rental-copy p{font-size:6px;line-height:1.5;margin:4px 0 8px}

  .hotel{top:800px;width:193px}
  .hotel .photo{height:76px}
  .hotel h4{font-size:6.5px;font-weight:700;color:var(--blue);margin-top:6px}
  .hotel .q{font-size:5.5px;color:var(--muted)}
  .hotel .stars{position:absolute;right:0;top:82px}
  .hotel p{font-size:5.5px;line-height:1.5;color:var(--muted);margin-top:5px}
  .hotel a{color:var(--orange);text-decoration:none;font-weight:600}

  .footer{left:0;top:944px;width:694px;height:138px;background:var(--blue)}
  .fcol{top:958px}
  .fcol h5{font-size:6.5px;font-weight:700;color:var(--orange);text-transform:uppercase;margin-bottom:6px;letter-spacing:.3px}
  .fcol li{list-style:none;color:var(--white);font-size:6px;line-height:1.75}
  .social{display:flex;gap:6px}
  .social i{width:10px;height:10px;border-radius:50%;background:rgba(255,255,255,.85)}
  .badge{left:560px;top:1026px;display:flex;align-items:center;gap:5px;border:1px solid rgba(255,255,255,.4);padding:4px 8px;color:var(--white);font-size:6px}
  .badge i{width:10px;height:10px;background:var(--orange)}
  .bottom{left:0;top:1082px;width:694px;height:32px;background:var(--blue-deep)}
  .support{left:64px;top:1088px;color:var(--white)}
  .support strong{font-size:7px;display:block}
  .support small{font-size:5.5px;opacity:.8}
  .copy{left:520px;top:1095px;color:var(--white);font-size:5.5px;opacity:.85}
  .totop{left:672px;top:1186px;color:var(--muted);font-size:5px}
</style>
</head>
<body>
  <div class="abs backdrop" role="img" aria-label="Tropical beach with turquoise sea, white sand and palm trees"></div>
  <div class="abs page"></div>

  <header>
    <div class="abs logo"><span>Caldera Key</span></div>
    <div class="abs topbar"></div>
    <div class="abs helpline">
      <svg width="10" height="10" viewBox="0 0 24 24"><path fill="#fff" d="M6.6 10.8a15 15 0 006.6 6.6l2.2-2.2c.3-.3.7-.4 1-.2 1.1.4 2.3.6 3.6.6.6 0 1 .4 1 1V20c0 .6-.4 1-1 1A17 17 0 013 4c0-.6.4-1 1-1h3.5c.6 0 1 .4 1 1 0 1.3.2 2.5.6 3.6.1.3 0 .7-.2 1z"/></svg>
      <small>HELPLINE</small><strong>1-800-555-0142</strong>
    </div>
    <div class="abs select" style="left:505px;width:38px"><span>USD $</span><span>▾</span></div>
    <div class="abs select" style="left:549px;width:88px"><span>Select Language</span><span>▾</span></div>
    <nav class="abs nav">
      <a class="active">Home</a><a>About Us</a><a>Tours</a><a>Hotels</a><a>Vehicles</a><a>Blog</a><a>Testimonials</a><a>Contact Us</a>
    </nav>
  </header>

  <section>
    <div class="abs hero" role="img" aria-label="Panama City skyline at night with a light-trailed coastal highway"></div>
    <div class="abs hero-road"></div>
    <div class="abs hero-copy">
      <h2>CENTRAL PANAMA</h2>
      <p>Welcome to the heart of Panama, where the<br>city meets the islands in one place</p>
      <span class="btn">LEARN MORE</span>
    </div>
    <div class="abs dots"><i></i><i></i><i class="on"></i><i></i><i></i></div>
  </section>

  <section>
    <h2 class="abs section-title" style="left:46px;top:372px">GUIDED TOURS</h2>
    <div class="abs arrows" style="left:617px;top:372px">
      <span><svg width="5" height="6" viewBox="0 0 5 6"><path d="M4 0L1 3l3 3" fill="none" stroke="#999"/></svg></span>
      <span><svg width="5" height="6" viewBox="0 0 5 6"><path d="M1 0l3 3-3 3" fill="none" stroke="#999"/></svg></span>
    </div>

    <article class="abs tour" style="left:46px">
      <div class="photo" role="img" aria-label="Old stone church tower ruins under a blue sky" style="background:linear-gradient(180deg,#7fb3de,#9a7a55 70%,#6d8a4a)"></div>
      <div class="abs ribbon"><b>HOT DEAL</b></div>
      <h3>Lorem ipsum is simply dummy<br>text of the printing</h3>
      <div class="rating stars">★★★★★<em>(33 Reviews)</em></div>
      <div class="meta"><small>Starts From</small><div class="price"><small>Price USD</small><strong>$ 59.99</strong></div></div>
    </article>

    <article class="abs tour" style="left:251px">
      <div class="photo" role="img" aria-label="Traveller on a tropical beach with clear turquoise water" style="background:linear-gradient(180deg,#6cc6e6,#2fb0c4 55%,#e8d6b0)"></div>
      <div class="abs ribbon"><b>HOT DEAL</b></div>
      <h3>It is a long established fact that<br>a reader will be</h3>
      <div class="rating stars">★★★★★<em>(33 Reviews)</em></div>
      <div class="meta"><small>Starts From</small><div class="price"><small>Price USD</small><strong>$ 59.99</strong></div></div>
    </article>

    <article class="abs tour" style="left:457px">
      <div class="photo" role="img" aria-label="Small island with palm trees surrounded by shallow sea" style="background:linear-gradient(180deg,#8fcbe8,#3aa9c8 50%,#5f9e5a 75%,#d9cfa8)"></div>
      <div class="abs ribbon"><b>HOT DEAL</b></div>
      <h3>There are many variations of<br>passages of lorem ipsum</h3>
      <div class="rating stars">★★★★★<em>(33 Reviews)</em></div>
      <div class="meta"><small>Starts From</small><div class="price"><small>Price USD</small><strong>$ 59.99</strong></div></div>
    </article>
  </section>

  <section>
    <div class="abs rental" role="img" aria-label="Row of parked rental cars"></div>
    <div class="abs rental-copy">
      <h2>RENTAL VEHICLES</h2>
      <p>Compare and reserve cars, jeeps and vans<br>for your stay on the island</p>
      <span class="btn">LEARN MORE</span>
    </div>
  </section>

  <section>
    <h2 class="abs section-title" style="left:46px;top:778px">HOTEL / HOSTELS</h2>
    <div class="abs arrows" style="left:617px;top:778px">
      <span><svg width="5" height="6" viewBox="0 0 5 6"><path d="M4 0L1 3l3 3" fill="none" stroke="#999"/></svg></span>
      <span><svg width="5" height="6" viewBox="0 0 5 6"><path d="M1 0l3 3-3 3" fill="none" stroke="#999"/></svg></span>
    </div>

    <article class="abs hotel" style="left:46px">
      <div class="photo" role="img" aria-label="Hotel bedroom with warm lighting" style="background:linear-gradient(180deg,#5a3a28,#a77a52 55%,#efe4d4)"></div>
      <h4>HOTEL NAME 1</h4><div class="q">Quality: 4/5</div>
      <div class="stars">★★★★☆</div>
      <p>There are many variations of passages of Lorem Ipsum available, but the majority have suffered. <a>Read More</a></p>
    </article>
    <article class="abs hotel" style="left:251px">
      <div class="photo" role="img" aria-label="Bright hotel room with double bed" style="background:linear-gradient(180deg,#9a6e44,#d9bd94 55%,#f5efe6)"></div>
      <h4>HOTEL NAME 2</h4><div class="q">Quality: 4/5</div>
      <div class="stars">★★★★☆</div>
      <p>There are many variations of passages of Lorem Ipsum available, but the majority have suffered. <a>Read More</a></p>
    </article>
    <article class="abs hotel" style="left:457px">
      <div class="photo" role="img" aria-label="Hotel suite with bed and lamps" style="background:linear-gradient(180deg,#4e3324,#a27c5a 55%,#e8dccb)"></div>
      <h4>HOTEL NAME 3</h4><div class="q">Quality: 4/5</div>
      <div class="stars">★★★★☆</div>
      <p>There are many variations of passages of Lorem Ipsum available, but the majority have suffered. <a>Read More</a></p>
    </article>
  </section>

  <footer>
    <div class="abs footer"></div>
    <div class="abs fcol" style="left:64px"><h5>Company</h5><ul><li>About us</li><li>Contact us</li><li>Tours</li><li>Hotels</li><li>Vehicles</li><li>News</li><li>Blog</li></ul></div>
    <div class="abs fcol" style="left:180px"><h5>Support</h5><ul><li>Customer Care</li><li>Privacy Policy</li><li>Low Price Guarantee</li><li>Group Services</li><li>Mileage Program</li></ul></div>
    <div class="abs fcol" style="left:300px"><h5>Top Destinations</h5><ul><li>Amsterdam Tours</li><li>Seattle Tours</li><li>Montreal Tours</li><li>Las Vegas Tours</li><li>Lisbon Tours</li><li>Madrid Tours</li><li>Melbourne Tours</li></ul></div>
    <div class="abs fcol" style="left:425px"><h5>Top Destinations</h5><ul><li>New York City Tours</li><li>Paris Tours</li><li>Rome Tours</li><li>San Francisco Tours</li><li>Sydney Tours</li><li>Tokyo Tours</li><li>Venice Tours</li></ul></div>
    <div class="abs fcol" style="left:560px"><h5>Follow us on</h5><div class="social"><i></i><i></i><i></i><i></i></div></div>
    <div class="abs badge"><i></i>Mileage Program</div>
    <div class="abs bottom"></div>
    <div class="abs support"><strong>24/7 Support</strong><small>1-800-555-0142</small></div>
    <div class="abs copy">Copyright © 2015 All Rights Reserved</div>
    <div class="abs totop">TOP</div>
  </footer>
</body>
</html>
```